Fairway Circuit web site

Fairway Circuit is a High End golf amateur Tour targeted to wealthy golf passionates.
The concept is to take average golfers and offer them the same playing conditions than the pros (Caddies, branded bags, TV coverage...) and bring them to the most beautiful golf courses around the world.
Keywords: International, Exclusive, Luxury, but not show-off...
The Task is to design the WordPress template and a exemple page.
Please use the provided logo and any stock image you like.
Updates

Hello,

please note that the outcome has to be a fully coded WordPress site.

Please no "Photoshop only" designs...

Thanks

```html
<!DOCTYPE html>
<html lang="en">
<head>
<meta charset="utf-8">
<title>Fairway Circuit</title>
<link href="https://fonts.googleapis.com/css2?family=Open+Sans:wght@400;600;700&display=swap" rel="stylesheet">
<style>
:root{
  --green-deep:#0a3d24;
  --green-dark:#0f4d2e;
  --green-mid:#1a6240;
  --green-accent:#2f8a58;
  --grass-light:#7aa552;
  --grass-dark:#2d5a1f;
  --ink:#2b2b2b;
  --muted:#7a7a7a;
  --panel-grey:#e6e6e6;
  --footer:#141414;
  --footer-text:#cfcfcf;
  --white:#ffffff;
}
*{margin:0;padding:0;box-sizing:border-box}
html,body{width:1200px;height:2496px;overflow:hidden}
body{font-family:"Open Sans",Arial,sans-serif;color:var(--ink);background:var(--white);position:relative}
.abs{position:absolute}

/* top utility bar */
.utility-bar{left:0;top:0;width:1200px;height:24px;background:var(--green-deep);border-bottom:1px solid #08311d}
.utility-links{left:180px;top:5px;font-size:10px;color:#cfe3d6}
.utility-links span{margin-right:12px}
.search-box{left:760px;top:4px;width:240px;height:16px;background:#0e4a2c;border:1px solid #1f6542;font-size:9px;color:#9bbfa9;padding:1px 6px}

/* header */
.site-header{left:0;top:24px;width:1200px;height:124px;background:linear-gradient(#11583a,#0b4128)}
.brand{left:170px;top:40px;display:flex;align-items:center;gap:12px}
.brand-mark{width:44px;height:44px;border-radius:50%;background:var(--green-accent);border:2px solid #cfe3d6}
.brand-name{font-size:20px;font-weight:600;color:var(--white)}
.main-nav{left:380px;top:103px;display:flex;gap:6px;font-size:11px;color:#e4efe8}
.main-nav a{padding:5px 11px;color:inherit;text-decoration:none}
.main-nav a.active{background:#06281a;border-radius:3px;color:var(--white)}

/* hero */
.hero{left:0;top:148px;width:1200px;height:592px;background:linear-gradient(#5d8a3c,var(--grass-light) 45%,var(--grass-dark))}
.hero-caption{left:200px;top:560px;width:640px;height:100px;background:rgba(20,30,20,.55);color:var(--white);font-size:25px;line-height:1.3;padding:18px 24px}
.hero-arrow{top:420px;width:28px;height:40px;background:rgba(0,0,0,.35)}

/* welcome */
.welcome-title{left:0;top:752px;width:1200px;text-align:center;font-size:24px;font-weight:600;color:var(--green-dark)}
.welcome-rule{left:520px;top:792px;width:160px;height:2px;background:var(--green-accent)}
.welcome-text{left:190px;top:808px;width:820px;text-align:center;font-size:12px;line-height:1.75;color:var(--muted)}

/* featured */
.featured{left:0;top:928px;width:1200px;height:292px;background:linear-gradient(var(--green-mid),var(--green-dark))}
.featured-label{left:0;top:950px;width:1200px;text-align:center;font-size:11px;font-weight:700;letter-spacing:1px;color:var(--white)}
.featured-label::before,.featured-label::after{content:"";display:inline-block;width:60px;height:1px;background:#8fc2a4;vertical-align:middle;margin:0 10px}
.feature-card{top:990px;width:220px}
.feature-photo{height:128px;border:3px solid var(--white)}
.feature-meta{font-size:9px;color:#b9d7c5;margin-top:6px;text-transform:uppercase}
.feature-title{font-size:11px;color:var(--white)}
.slide-arrow{width:22px;height:30px;background:#06281a}

/* panels */
.panel{top:1260px;width:260px;height:300px;background:#f1f1f1;border:1px solid #d6d6d6}
.panel-head{height:38px;background:var(--green-dark);color:var(--white);font-size:13px;font-weight:600;padding:10px 14px}
.panel-photo{height:260px}
.panel-overlay{left:0;bottom:0;width:100%;padding:10px 14px;background:rgba(0,0,0,.45);color:var(--white);font-size:11px}
.tour-body{padding:20px 16px;font-size:11px;color:var(--muted);line-height:1.7}
.tour-name{font-size:13px;color:var(--ink);font-weight:600}

/* news */
.news{left:0;top:1590px;width:1200px;height:630px;background:linear-gradient(#f4f4f4,var(--panel-grey))}
.section-title{left:0;width:1200px;text-align:center;font-size:20px;font-weight:600;color:var(--green-dark)}
.news-rule{left:530px;top:1670px;width:140px;height:2px;background:var(--green-accent)}
.news-card{width:240px;height:220px;background:var(--white);border:1px solid #d8d8d8;padding:8px}
.news-photo{height:132px}
.news-tag{font-size:9px;font-weight:700;color:var(--green-accent);margin-top:8px}
.news-text{font-size:11px;color:var(--muted);line-height:1.6;margin-top:2px}

/* partners */
.partner-rule{left:540px;top:2270px;width:120px;height:2px;background:var(--green-accent)}
.partner-strip{left:180px;top:2296px;width:840px;height:70px;display:flex;align-items:center;justify-content:space-between;padding:0 40px;border-top:1px solid #e2e2e2;border-bottom:1px solid #e2e2e2}
.partner-badge{width:110px;height:40px;border-radius:4px;background:#d9d9d9}

/* footer */
.site-footer{left:0;top:2400px;width:1200px;height:96px;background:var(--footer)}
.footer-links{left:180px;top:2420px;font-size:10px;color:var(--footer-text)}
.footer-links span{margin-right:10px}
.copyright{left:180px;top:2440px;font-size:9px;color:#9a9a9a}
.social{top:2414px;width:22px;height:22px;border-radius:3px;background:#3a6ea5}
</style>
</head>
<body>

<div class="abs utility-bar"></div>
<div class="abs utility-links"><span>Login</span><span>Register</span><span>Store</span></div>
<div class="abs search-box">Search</div>

<header class="abs site-header"></header>
<div class="abs brand"><div class="brand-mark"></div><div class="brand-name">Fairway Circuit</div></div>
<nav class="abs main-nav">
  <a class="active">Home</a><a>About Us</a><a>Players</a><a>Tournaments</a><a>Stats</a><a>Gallery</a><a>News</a><a>Contact Us</a>
</nav>

<section class="abs hero" role="img" aria-label="Close view of a gloved hand placing a golf ball on a tee over green grass"></section>
<svg class="abs hero-arrow" style="left:0" viewBox="0 0 28 40"><path d="M17 13l-7 7 7 7" stroke="#fff" stroke-width="2" fill="none"/></svg>
<svg class="abs hero-arrow" style="left:1172px" viewBox="0 0 28 40"><path d="M11 13l7 7-7 7" stroke="#fff" stroke-width="2" fill="none"/></svg>
<div class="abs hero-caption">Duis aute irure dolor in reprehenderit in voluptate velit esse cillum</div>

<h1 class="abs welcome-title">Welcome To Fairway Circuit</h1>
<div class="abs welcome-rule"></div>
<p class="abs welcome-text">Our members play where the professionals play, with caddies, tour bags and television crews on every round. Each season we travel to celebrated courses across the globe, pairing quiet luxury with honest competition. Join a circle of passionate amateurs who value the game, the company and the landscape far more than the spotlight.</p>

<section class="abs featured"></section>
<div class="abs featured-label">FEATURED CONTENT</div>
<svg class="abs slide-arrow" style="left:200px;top:1040px" viewBox="0 0 22 30"><path d="M13 10l-5 5 5 5" stroke="#fff" stroke-width="2" fill="none"/></svg>
<svg class="abs slide-arrow" style="left:978px;top:1040px" viewBox="0 0 22 30"><path d="M9 10l5 5-5 5" stroke="#fff" stroke-width="2" fill="none"/></svg>
<div class="abs feature-card" style="left:250px">
  <div class="feature-photo" role="img" aria-label="Portrait of a tour player on the course" style="background:linear-gradient(#9fb8c8,#6f8f5a)"></div>
  <div class="feature-meta">Open Week</div><div class="feature-title">Links at Dawn</div>
</div>
<div class="abs feature-card" style="left:490px">
  <div class="feature-photo" role="img" aria-label="Video still of a player mid swing" style="background:linear-gradient(#b7c9a6,#4f7a38)"></div>
  <div class="feature-meta">Swing Clinic</div><div class="feature-title">Caddie Day Recap</div>
</div>
<div class="abs feature-card" style="left:730px">
  <div class="feature-photo" role="img" aria-label="Two golfers posing together at an invitational" style="background:linear-gradient(#8aa0b4,#4d6a3c)"></div>
  <div class="feature-meta">Final Round</div><div class="feature-title">Harbor Pines Invitational</div>
</div>

<div class="abs panel" style="left:180px">
  <div class="panel-head">Meet The Players</div>
  <div class="panel-photo" role="img" aria-label="Smiling player holding a club on the fairway" style="position:relative;background:linear-gradient(#b9cbd6,#7c9a62)">
    <div class="abs panel-overlay"><b>Marco Ellery</b><br>United States</div>
  </div>
</div>
<div class="abs panel" style="left:470px">
  <div class="panel-head">Gallery</div>
  <div class="panel-photo" role="img" aria-label="Golfer following through after a drive" style="position:relative;background:linear-gradient(#c9d6c0,#5e8a44)">
    <div class="abs panel-overlay"><b>Season Album</b><br>Spain</div>
  </div>
</div>
<div class="abs panel" style="left:760px">
  <div class="panel-head">Upcoming Tours</div>
  <div class="tour-body">
    <div class="tour-name">Tour Name</div>
    Three rounds on a cliffside course by the sea.<br><br>
    <svg width="10" height="12" viewBox="0 0 10 12" style="vertical-align:middle"><path d="M5 0a4 4 0 014 4c0 3-4 8-4 8S1 7 1 4a4 4 0 014-4z" fill="#2f8a58"/></svg> Eastgate Links<br>
    <svg width="10" height="10" viewBox="0 0 10 10" style="vertical-align:middle"><rect x="1" y="2" width="8" height="7" fill="none" stroke="#2f8a58"/></svg> 28th Mar 2014, 10:00AM
  </div>
</div>

<section class="abs news"></section>
<h2 class="abs section-title" style="top:1632px">Our News Feed</h2>
<div class="abs news-rule"></div>

<div class="abs news-card" style="left:200px;top:1694px"><div class="news-photo" role="img" aria-label="Players shaking hands on the green" style="background:linear-gradient(#a8bccb,#5a7f45)"></div><div class="news-tag">INTERVIEW</div><div class="news-text">Friday evening on-site recap from the clubhouse</div></div>
<div class="abs news-card" style="left:480px;top:1694px"><div class="news-photo" role="img" aria-label="Golfer lining up a putt" style="background:linear-gradient(#b5c6b0,#4e7537)"></div><div class="news-tag">INTERVIEW</div><div class="news-text">Friday evening on-site recap from the clubhouse</div></div>
<div class="abs news-card" style="left:760px;top:1694px"><div class="news-photo" role="img" aria-label="Crowd gathered at a trophy ceremony" style="background:linear-gradient(#c8b8a8,#6a8c50)"></div><div class="news-tag">INTERVIEW</div><div class="news-text">Friday evening on-site recap from the clubhouse</div></div>
<div class="abs news-card" style="left:200px;top:1950px"><div class="news-photo" role="img" aria-label="Golfer swinging on a tree-lined fairway" style="background:linear-gradient(#9db28e,#3f6a2e)"></div><div class="news-tag">INTERVIEW</div><div class="news-text">Friday evening on-site recap from the clubhouse</div></div>
<div class="abs news-card" style="left:480px;top:1950px"><div class="news-photo" role="img" aria-label="Player in blue shirt watching his shot" style="background:linear-gradient(#a9c0d2,#5b8247)"></div><div class="news-tag">INTERVIEW</div><div class="news-text">Friday evening on-site recap from the clubhouse</div></div>
<div class="abs news-card" style="left:760px;top:1950px"><div class="news-photo" role="img" aria-label="Senior player at a press moment" style="background:linear-gradient(#bfc8cf,#6d8a5a)"></div><div class="news-tag">INTERVIEW</div><div class="news-text">Friday evening on-site recap from the clubhouse</div></div>

<h2 class="abs section-title" style="top:2236px">Partners</h2>
<div class="abs partner-rule"></div>
<div class="abs partner-strip">
  <svg width="14" height="20" viewBox="0 0 14 20"><path d="M10 4l-6 6 6 6" stroke="#555" stroke-width="2" fill="none"/></svg>
  <div class="partner-badge"></div><div class="partner-badge"></div><div class="partner-badge"></div><div class="partner-badge"></div><div class="partner-badge"></div>
  <svg width="14" height="20" viewBox="0 0 14 20"><path d="M4 4l6 6-6 6" stroke="#555" stroke-width="2" fill="none"/></svg>
</div>

<footer class="abs site-footer"></footer>
<div class="abs footer-links"><span>Home</span><span>Disclaimer</span><span>Terms of Conditions</span><span>Privacy Policy</span><span>About Us</span><span>Contact</span></div>
<div class="abs copyright">© 2014 Fairway Circuit. All rights reserved.</div>
<div class="abs social" style="left:904px"></div>
<div class="abs social" style="left:932px;background:#3aa3d8"></div>
<div class="abs social" style="left:960px;background:#c8463a"></div>
<div class="abs social" style="left:988px;background:#2a6f9e"></div>

</body>
</html>
```